Business Card Design Project

Business Card
We are rebranding with a new logo
Industry/Entity Type
Business
Contact Information for Business Card
Dennis Morvale +61 487215963 dennis@quorv.com.au P.O. Box 872 Fernlow QLD 4309
Requirements
Must have
- Logo

```html
<!DOCTYPE html>
<html lang="en">
<head>
<meta charset="UTF-8">
<title>Quorv International – Business Card</title>
<link rel="stylesheet" href="https://fonts.googleapis.com/css2?family=Lato:wght@400;700&family=Arimo:wght@400&display=swap">
<style>
  :root {
    --backdrop: #c9c8c9;
    --card: #ffffff;
    --ink: #111111;
    --muted: #4a4a4a;
    --brand: #1b72ad;
    --icon: #5cbfe9;
  }
  * { margin: 0; padding: 0; box-sizing: border-box; }
  html, body {
    width: 1200px; height: 1000px; overflow: hidden;
    background: var(--backdrop);
  }
  .canvas {
    position: relative; width: 1200px; height: 1000px;
  }
  .card {
    position: absolute; left: 220px; top: 282px;
    width: 761px; height: 435px;
    background: var(--card);
    box-shadow: 0 10px 24px rgba(0,0,0,0.25);
  }
  .brand {
    position: absolute; left: 78px; top: 196px;
    display: flex; align-items: center; gap: 12px;
  }
  .brand-dot {
    width: 22px; height: 22px; border-radius: 50%;
    background: var(--brand);
  }
  .brand-name {
    font-family: "Lato", sans-serif; font-weight: 700;
    font-size: 26px; color: var(--brand); letter-spacing: 0.5px;
  }
  .holder {
    position: absolute; left: 475px; top: 70px;
    font-family: "Lato", sans-serif; font-size: 30px;
    color: var(--ink); letter-spacing: 1px;
  }
  .holder .first { font-weight: 700; }
  .holder .last { font-weight: 400; }
  .contact {
    position: absolute; left: 475px;
    display: flex; align-items: flex-start; gap: 16px;
  }
  .contact svg { flex: none; width: 34px; height: 34px; }
  .contact-text {
    font-family: "Arimo", sans-serif; font-size: 16px;
    color: var(--muted); letter-spacing: 1.4px; word-spacing: 4px;
    line-height: 23px; padding-top: 1px;
  }
  .contact.phone { top: 159px; }
  .contact.email { top: 221px; }
  .contact.post  { top: 287px; }
</style>
</head>
<body>
<div class="canvas">
  <div class="card">
    <div class="brand">
      <span class="brand-dot"></span>
      <span class="brand-name">Quorv International</span>
    </div>

    <div class="holder"><span class="first">Dennis</span> <span class="last">Morvale</span></div>

    <div class="contact phone">
      <svg viewBox="0 0 34 34" aria-hidden="true">
        <circle cx="17" cy="17" r="17" fill="var(--icon)"/>
        <path d="M12 9c1-.6 2-.3 2.5.6l1.3 2.4c.4.8.2 1.6-.5 2.1l-1 .7c.8 2 2.3 3.6 4.2 4.6l.8-1c.5-.6 1.4-.8 2.1-.4l2.4 1.4c.8.5 1.1 1.5.5 2.4l-.9 1.3c-.7 1-2 1.4-3.2 1-5-1.8-8.7-5.6-10.3-10.6-.4-1.2 0-2.5 1-3.2z" fill="#fff"/>
      </svg>
      <span class="contact-text">+61 487215963</span>
    </div>

    <div class="contact email">
      <svg viewBox="0 0 34 34" aria-hidden="true">
        <circle cx="17" cy="17" r="17" fill="var(--icon)"/>
        <rect x="8" y="11" width="18" height="12" rx="1" fill="#fff"/>
        <path d="M8.5 11.5 17 18l8.5-6.5" fill="none" stroke="var(--icon)" stroke-width="1.3"/>
      </svg>
      <span class="contact-text">dennis@quorv.com.au</span>
    </div>

    <div class="contact post">
      <svg viewBox="0 0 34 34" aria-hidden="true">
        <circle cx="17" cy="17" r="17" fill="var(--icon)"/>
        <g fill="none" stroke="#fff" stroke-width="1.4">
          <circle cx="17" cy="17" r="9"/>
          <ellipse cx="17" cy="17" rx="4" ry="9"/>
          <line x1="8" y1="17" x2="26" y2="17"/>
          <path d="M9.5 12.5h15M9.5 21.5h15"/>
        </g>
      </svg>
      <span class="contact-text">P.O. Box 872<br>Fernlow QLD 4309</span>
    </div>
  </div>
</div>
</body>
</html>
```